Website Landing Page Kestrel Plumbing

Dear Contestants,

I would like you to design me a landing page for my new website. I have attached a screen shot of my current website which is being constructed.

I do not want the lay out to change at all as my web designer has put this system together and the layout cannot change.

-I would like a designer to come up with something creative and appealing. I would like the website to be classy and elegant.

-I have also attached my flyer design etc so you get an idea of colours etc.

Also I have files etc of logo etc and photos if you would like me to email them that is no issue.

I am happy to provide more info if you request at anytime.

If anyone needs files I can email photos etc. Please reach out.

Industry/Entity Type

Plumbing

```html
<!DOCTYPE html>
<html lang="en">
<head>
<meta charset="utf-8">
<title>Kestrel Plumbing – Landing Page</title>
<link rel="stylesheet" href="https://fonts.googleapis.com/css2?family=Montserrat:wght@500;600;700;800&display=swap">
<style>
  :root {
    --teal: #0a9ec7;
    --navy: #1b3d8f;
    --blue: #1f8bd8;
    --ink: #111111;
    --field: #e2e2e2;
    --white: #ffffff;
  }
  * { margin: 0; padding: 0; box-sizing: border-box; }
  html, body { width: 960px; height: 1200px; overflow: hidden; }
  body { position: relative; background: var(--white); font-family: "Montserrat", sans-serif; color: var(--ink); }
  .abs { position: absolute; }

  .top-bar { left: 0; top: 0; width: 960px; height: 34px; background: var(--teal); }
  .social { position: absolute; top: 5px; width: 24px; height: 24px; border-radius: 50%; background: #111; border: 2px solid #333; }

  .brand { left: 104px; top: 68px; font-size: 14px; font-weight: 800; color: var(--navy); display: flex; align-items: center; gap: 6px; }
  .brand-dot { width: 14px; height: 14px; background: var(--teal); border-radius: 50%; }

  .nav { top: 70px; font-size: 10px; font-weight: 600; color: var(--navy); letter-spacing: .3px; }
  .nav-home { left: 310px; top: 70px; width: 47px; height: 18px; border-radius: 9px; background: #111; color: var(--white); font-size: 10px; font-weight: 600; display: flex; align-items: center; justify-content: center; }
  .nav-book { left: 606px; top: 66px; width: 78px; height: 26px; background: var(--teal); color: var(--white); font-size: 10px; font-weight: 600; display: flex; align-items: center; justify-content: center; }
  .phone-badge { left: 748px; top: 60px; width: 32px; height: 32px; border-radius: 50%; background: var(--white); box-shadow: 0 2px 5px rgba(0,0,0,.25); display: flex; align-items: center; justify-content: center; }
  .phone-num { left: 784px; top: 72px; font-size: 8px; font-weight: 600; color: var(--navy); }
  .phone-care { left: 784px; top: 83px; font-size: 5px; font-weight: 700; }

  .hero { left: 96px; top: 108px; width: 769px; height: 303px; background: linear-gradient(100deg, #1f6fd6 0%, #3a86de 28%, #cdd7df 40%, #e4e9ee 70%, #dde3e8 100%); }
  .hero-line1 { left: 398px; top: 196px; font-size: 26px; font-weight: 800; color: var(--navy); letter-spacing: 1.5px; }
  .hero-line2 { left: 494px; top: 233px; font-size: 26px; font-weight: 800; color: var(--blue); letter-spacing: 1.5px; }
  .hero-btn { left: 470px; top: 298px; width: 160px; height: 33px; background: var(--white); color: var(--blue); font-size: 15px; font-weight: 800; letter-spacing: 1px; display: flex; align-items: center; justify-content: center; }
  .dot { position: absolute; border-radius: 50%; background: var(--white); }

  .intro-title { left: 98px; top: 483px; width: 250px; font-size: 20px; font-weight: 700; text-align: center; line-height: 25px; letter-spacing: .5px; }
  .intro-title span { color: var(--blue); }
  .intro-text { left: 103px; top: 543px; width: 245px; font-size: 10px; font-weight: 600; line-height: 18.5px; }
  .outline-btn { left: 154px; top: 704px; width: 123px; height: 28px; border: 1.5px solid var(--blue); color: var(--navy); font-size: 11px; font-weight: 600; display: flex; align-items: center; justify-content: center; letter-spacing: .5px; }

  .section-title { font-size: 20px; font-weight: 700; letter-spacing: .8px; transform: translateX(-50%); white-space: nowrap; }
  .section-title span { color: var(--blue); }
  .rule { height: 2px; background: var(--navy); }

  .feat-icon { width: 46px; height: 46px; border-radius: 50%; background: var(--white); box-shadow: 0 1px 5px rgba(0,0,0,.25); display: flex; align-items: center; justify-content: center; }
  .feat-title { font-size: 14px; font-weight: 700; color: var(--navy); letter-spacing: .8px; }
  .feat-text { font-size: 8.5px; font-weight: 500; line-height: 13.5px; width: 180px; }

  .worker { left: 92px; top: 796px; width: 104px; height: 272px; background: linear-gradient(180deg, #c9cfd8 0%, #2d5fd0 35%, #1f4fc0 80%, #333 100%); border-radius: 40px 40px 8px 8px; }
  .service-list { left: 226px; top: 886px; list-style: none; font-size: 11px; font-weight: 700; letter-spacing: .4px; }
  .service-list li { height: 24px; display: flex; align-items: center; gap: 10px; }

  .request { left: 516px; top: 762px; width: 342px; height: 343px; background: var(--white); box-shadow: 0 0 14px rgba(60,140,230,.55); }
  .request-title { left: 686px; top: 780px; font-size: 21px; font-weight: 700; letter-spacing: .8px; transform: translateX(-50%); white-space: nowrap; }
  .request-title span { color: var(--blue); }
  .field { background: var(--field); box-shadow: inset 0 0 6px rgba(0,0,0,.12); font-size: 12.5px; font-weight: 500; letter-spacing: .8px; color: #333; padding-left: 12px; display: flex; align-items: center; }
  .field-area { align-items: flex-start; padding-top: 18px; }
  .quote-btn { left: 607px; top: 1063px; width: 194px; height: 31px; background: var(--teal); color: var(--white); font-size: 15px; font-weight: 800; letter-spacing: .8px; display: flex; align-items: center; justify-content: center; }

  .footer { left: 0; top: 1124px; width: 960px; height: 76px; background: var(--teal); }
  .foot-link { top: 1152px; font-size: 10px; font-weight: 700; color: var(--white); letter-spacing: .3px; }
</style>
</head>
<body>
  <div class="abs top-bar">
    <span class="social" style="left:748px"></span>
    <span class="social" style="left:776px"></span>
    <span class="social" style="left:804px"></span>
    <span class="social" style="left:832px"></span>
  </div>

  <div class="abs brand"><span class="brand-dot"></span>Kestrel Plumbing</div>

  <div class="abs nav-home">HOME</div>
  <div class="abs nav" style="left:369px">SERVICES</div>
  <div class="abs nav" style="left:443px">ABOUT US</div>
  <div class="abs nav" style="left:522px">CONTACT US</div>
  <div class="abs nav-book">BOOK NOW</div>

  <div class="abs phone-badge">
    <svg width="16" height="16" viewBox="0 0 24 24" fill="none" stroke="#1f8bd8" stroke-width="1.6"><path d="M5 3h4l2 5-2.5 1.5a11 11 0 0 0 6 6L16 13l5 2v4a2 2 0 0 1-2 2A17 17 0 0 1 3 5a2 2 0 0 1 2-2z"/></svg>
  </div>
  <div class="abs phone-num">1300-482-319</div>
  <div class="abs phone-care">24*7 CUSTOMER CARE</div>

  <div class="abs hero" role="img" aria-label="Photo of plumbing tools, pipes, taps and fittings laid on a blue mat and pale wooden surface"></div>
  <div class="abs hero-line1">LOCAL AFFORDABLE</div>
  <div class="abs hero-line2">PLUMBING SOLUTIONS</div>
  <div class="abs hero-btn">LEARN MORE</div>
  <span class="dot" style="left:453px;top:375px;width:10px;height:10px"></span>
  <span class="dot" style="left:469px;top:370px;width:18px;height:18px;background:var(--blue)"></span>
  <span class="dot" style="left:496px;top:375px;width:10px;height:10px"></span>

  <h2 class="abs intro-title">EVERYDAY <span>LOWCOST PLUMBING</span></h2>
  <div class="abs intro-text">
    <p>Lorem ipsum dolor sit amet, csectetur adipisicing elit, sed do eiu mod tempor incididunt ut labore et dolore magna aliqua.</p>
    <p style="margin-top:18px">Ut enim ad minim veniam, quis nostrud exercitation ullamco laboris nis-iutaliquip ex ea commodo. consequat.</p>
  </div>
  <div class="abs outline-btn">SEE MORE</div>

  <h2 class="abs section-title" style="left:610px;top:483px">OUR FEATURES</h2>
  <div class="abs rule" style="left:586px;top:512px;width:48px"></div>

  <div class="abs feat-icon" style="left:373px;top:549px">
    <svg width="20" height="22" viewBox="0 0 20 22" fill="none" stroke="#1aa7c9" stroke-width="2"><path d="M3 2h14M3 20h14M5 2c0 6 10 6 10 9s-10 3-10 9M15 2c0 6-10 6-10 9"/></svg>
  </div>
  <div class="abs feat-title" style="left:428px;top:546px">EFFICIENT</div>
  <div class="abs feat-text" style="left:430px;top:570px">We won't waste your time we pride ourselves on solving your problem</div>

  <div class="abs feat-icon" style="left:621px;top:547px">
    <svg width="22" height="22" viewBox="0 0 24 24" fill="none" stroke="#1aa7c9" stroke-width="2.2"><path d="M14 4a5 5 0 0 0 5 7l-9 9-3-3 9-9a5 5 0 0 1-2-4z"/></svg>
  </div>
  <div class="abs feat-title" style="left:682px;top:546px">RELIABLE</div>
  <div class="abs feat-text" style="left:682px;top:566px">We arrive on time and come prepared our vans are stocked to handle your issue.</div>

  <div class="abs feat-icon" style="left:375px;top:649px">
    <svg width="22" height="20" viewBox="0 0 22 20" fill="#1aa7c9"><circle cx="6" cy="5" r="3"/><circle cx="16" cy="5" r="3"/><circle cx="11" cy="7" r="3.4"/><rect x="2" y="11" width="18" height="8" rx="3"/></svg>
  </div>
  <div class="abs feat-title" style="left:431px;top:647px">AFFORDABLE</div>
  <div class="abs feat-text" style="left:433px;top:670px">We pice competitively and never overcharge.our billing process is transparent.</div>

  <div class="abs feat-icon" style="left:621px;top:643px">
    <svg width="16" height="24" viewBox="0 0 16 24" fill="none" stroke="#1aa7c9" stroke-width="2.2"><path d="M8 1v22M13 6c-1-2-3-2.5-5-2.5S3 5 3 7.5 6 10.5 8 11s5 1.5 5 4.5-2.5 4-5 4-4.5-1-5-3"/></svg>
  </div>
  <div class="abs feat-title" style="left:677px;top:641px">RESPECTFULL</div>
  <div class="abs feat-text" style="left:679px;top:663px">We value our customers and treat them with respect we'll always leave your home tidy.</div>

  <div class="abs worker" role="img" aria-label="Photo of a plumber in blue overalls and hard hat holding a wrench and toolbox"></div>

  <h2 class="abs section-title" style="left:360px;top:823px">OUR <span>SEVICES</span></h2>
  <div class="abs rule" style="left:338px;top:852px;width:48px"></div>

  <ul class="abs service-list">
    <li><svg width="9" height="12" viewBox="0 0 9 12"><path d="M4.5 0C3 3 0 5.5 0 8a4.5 4 0 0 0 9 0C9 5.5 6 3 4.5 0z" fill="#1f8bd8"/></svg>Same Day Service</li>
    <li><svg width="9" height="12" viewBox="0 0 9 12"><path d="M4.5 0C3 3 0 5.5 0 8a4.5 4 0 0 0 9 0C9 5.5 6 3 4.5 0z" fill="#1f8bd8"/></svg>Blocked Drains</li>
    <li><svg width="9" height="12" viewBox="0 0 9 12"><path d="M4.5 0C3 3 0 5.5 0 8a4.5 4 0 0 0 9 0C9 5.5 6 3 4.5 0z" fill="#1f8bd8"/></svg>Hot Water</li>
    <li><svg width="9" height="12" viewBox="0 0 9 12"><path d="M4.5 0C3 3 0 5.5 0 8a4.5 4 0 0 0 9 0C9 5.5 6 3 4.5 0z" fill="#1f8bd8"/></svg>Burst pipe,Leakingtaps &amp; Toilets</li>
    <li><svg width="9" height="12" viewBox="0 0 9 12"><path d="M4.5 0C3 3 0 5.5 0 8a4.5 4 0 0 0 9 0C9 5.5 6 3 4.5 0z" fill="#1f8bd8"/></svg>Gas Installations</li>
    <li><svg width="9" height="12" viewBox="0 0 9 12"><path d="M4.5 0C3 3 0 5.5 0 8a4.5 4 0 0 0 9 0C9 5.5 6 3 4.5 0z" fill="#1f8bd8"/></svg>Leak Detection</li>
    <li><svg width="9" height="12" viewBox="0 0 9 12"><path d="M4.5 0C3 3 0 5.5 0 8a4.5 4 0 0 0 9 0C9 5.5 6 3 4.5 0z" fill="#1f8bd8"/></svg>Emergency Service</li>
  </ul>

  <div class="abs request"></div>
  <h2 class="abs request-title"><span>SERVICE</span> REQUEST</h2>
  <div class="abs field" style="left:549px;top:830px;width:146px;height:36px">NAME</div>
  <div class="abs field" style="left:701px;top:830px;width:133px;height:36px">PHONE NO.</div>
  <div class="abs field" style="left:549px;top:887px;width:285px;height:36px">EMAIL ADDRESS</div>
  <div class="abs field field-area" style="left:547px;top:946px;width:285px;height:108px">DESCRIPTION HERE</div>
  <div class="abs quote-btn">GET QUOTE</div>

  <div class="abs footer"></div>
  <div class="abs foot-link" style="left:302px">HOME</div>
  <div class="abs foot-link" style="left:355px">SERVICES</div>
  <div class="abs foot-link" style="left:429px">ABOUT US</div>
  <div class="abs foot-link" style="left:508px">CONTACT US</div>
  <div class="abs foot-link" style="left:598px">BOOK NOW</div>
</body>
</html>
```